Business cards and stationary design

We just completed the design of our new logo and we need to print new business cards and letterhead for our nonprofit. We are looking for a fresh new design that shows off our new logo. On letterhead, we must have a column on the right or left to include our Board of Directors (up to 45 names) (see attachment)

Industry/Entity Type

Non-Profit

Contact Information for Business Card

Standard business card with name, title, Company name, mailing address phone numbers, email address and website. Tagline on back "Bringing the homeless home"

Font styles to use
Sans Serif

Requirements
Must have
• include pertinent information above
• new logo
• fonts compatible with logo
• should use logo colors only
Nice to have
• tag lines

```html
<!DOCTYPE html>
<html lang="en">
<head>
<meta charset="utf-8">
<title>Homeward Crossing – Business Card</title>
<link rel="stylesheet" href="https://fonts.googleapis.com/css2?family=Courier+Prime:wght@400;700&display=swap">
<style>
  :root {
    --backdrop: #e9e6e3;
    --card: #ffffff;
    --ink: #3a3a3a;
    --ink-soft: #555555;
    --teal: #0a86a4;
    --amber: #fbb52b;
    --red: #ed1c24;
  }
  * { box-sizing: border-box; margin: 0; padding: 0; }
  html, body {
    width: 1200px; height: 900px; overflow: hidden;
    background: var(--backdrop);
    font-family: "Courier Prime", "Courier New", monospace;
    color: var(--ink);
  }
  .stage { position: relative; width: 1200px; height: 900px; }
  .card {
    position: absolute;
    background: var(--card);
    box-shadow: 0 6px 18px rgba(0,0,0,0.12);
    overflow: hidden;
    text-align: center;
  }
  .card--front { left: 150px; top: 70px; width: 588px; height: 364px; }
  .card--back  { left: 388px; top: 505px; width: 567px; height: 352px; }

  .color-bar {
    position: absolute; left: 0; right: 0; bottom: 0; height: 19px;
    display: flex; gap: 2px; background: var(--card);
  }
  .color-bar span { flex: 1; }
  .color-bar .teal  { background: var(--teal); }
  .color-bar .amber { background: var(--amber); }
  .color-bar .red   { background: var(--red); }

  .front-content {
    position: absolute; left: 0; right: 0; top: 68px;
    padding-left: 0;
  }
  .person-name { font-weight: 700; font-size: 20px; line-height: 24px; color: var(--ink); }
  .person-title { font-size: 16px; line-height: 20px; color: var(--ink-soft); }
  .contact-list { list-style: none; margin-top: 14px; font-size: 16px; line-height: 21.5px; color: var(--ink-soft); }
  .org-name--small {
    margin-top: 18px; font-size: 27px; line-height: 32px; color: var(--teal); font-weight: 400;
  }
  .address { margin-top: 10px; font-size: 16px; line-height: 21px; color: var(--ink-soft); }

  .back-content { position: absolute; left: 0; right: 0; top: 186px; }
  .org-name--large { font-size: 40px; line-height: 46px; color: var(--teal); font-weight: 400; }
  .tagline {
    margin-top: 32px; font-size: 17px; font-weight: 700; letter-spacing: 0.5px; color: var(--ink-soft);
  }
</style>
</head>
<body>
<main class="stage">
  <section class="card card--front" aria-label="Business card front">
    <div class="front-content">
      <p class="person-name">Daniel Hart</p>
      <p class="person-title">Managing Director</p>
      <ul class="contact-list">
        <li>(051)987654321</li>
        <li>hello@homewardcrossing.org</li>
        <li>www.homewardcrossing.org</li>
      </ul>
      <p class="org-name--small">Homeward Crossing</p>
      <p class="address">418, Harbor Lane<br>Riverton, 50721</p>
    </div>
    <div class="color-bar"><span class="teal"></span><span class="amber"></span><span class="red"></span></div>
  </section>

  <section class="card card--back" aria-label="Business card back">
    <div class="back-content">
      <p class="org-name--large">Homeward Crossing</p>
      <p class="tagline">Bringing the homeless home</p>
    </div>
    <div class="color-bar"><span class="teal"></span><span class="amber"></span><span class="red"></span></div>
  </section>
</main>
</body>
</html>
```